Income Tax Business Cards - Updates

Need to update these business cards while keeping all the same wording but just update them and make them look nicer and more modern/ on brand with our brand.

Industry/Entity Type

finance

Contact Information for Business Card

we have multiple locations so will just need to easily be able to change the address and phone numbers

Colors

Designer to choose colors to be used in the design.

```html
<!DOCTYPE html>
<html lang="en">
<head>
<meta charset="utf-8">
<title>Northgate Financial – Tax Business Cards</title>
<link rel="stylesheet" href="https://fonts.googleapis.com/css2?family=Montserrat:wght@400;500;700;800&display=swap">
<style>
  :root {
    --brand-green: #0d5230;
    --brand-red: #c41e26;
    --paper: #ffffff;
    --ink: #3a3a3a;
    --backdrop: #999999;
  }
  * { margin: 0; padding: 0; box-sizing: border-box; }
  html, body {
    width: 1200px; height: 1059px; overflow: hidden;
    background: var(--backdrop);
    font-family: "Montserrat", sans-serif;
  }
  .card {
    position: absolute;
    border-radius: 24px;
    overflow: hidden;
  }
  .line {
    position: absolute; left: 0; right: 0;
    text-align: center; white-space: nowrap;
    font-weight: 700; line-height: 1;
  }

  /* Front card */
  .card-front {
    left: 256px; top: 89px; width: 687px; height: 390px;
    background: var(--paper);
  }
  .card-front .hill { position: absolute; left: 0; top: 0; }
  .brand {
    position: absolute; left: 118px; top: 152px; width: 228px;
    text-align: right;
    font-weight: 700; font-size: 25px; color: var(--brand-green);
    line-height: 1.15;
  }
  .brand-mark {
    display: inline-block; width: 12px; height: 12px;
    background: var(--brand-red); margin-right: 8px; vertical-align: 2px;
  }
  .divider {
    position: absolute; left: 367px; top: 45px; width: 2px; height: 110px;
    background: var(--brand-red);
  }
  .address {
    position: absolute; left: 397px; top: 45px;
    font-size: 19px; font-weight: 400; color: var(--ink);
    line-height: 27px; letter-spacing: 0.3px;
  }
  .phone {
    position: absolute; left: 397px; top: 129px;
    display: flex; align-items: center; gap: 7px;
    font-size: 22px; font-weight: 700; color: var(--brand-green);
  }
  .badge {
    position: absolute; left: 179px; top: 182px; width: 329px; height: 48px;
    border-radius: 24px; background: var(--brand-red);
    color: var(--paper); font-weight: 700; font-size: 31px;
    display: flex; align-items: center; justify-content: center;
  }
  .front-amount { top: 234px; font-size: 61px; color: var(--paper); }
  .front-amount .figure { color: var(--brand-red); }
  .front-advance { top: 295px; font-size: 37px; color: var(--paper); }
  .front-note { top: 345px; font-size: 16px; font-weight: 600; color: var(--paper); }

  /* Back card */
  .card-back {
    left: 253px; top: 569px; width: 694px; height: 394px;
    background: var(--brand-red);
  }
  .back-top {
    position: absolute; left: 0; top: 0; width: 100%; height: 202px;
    background: var(--brand-green);
  }
  .back-rule {
    position: absolute; left: 0; top: 202px; width: 100%; height: 6px;
    background: var(--paper);
  }
  .back-file { top: 39px; font-size: 77px; color: var(--paper); }
  .back-taxes { top: 110px; font-size: 77px; color: var(--brand-red); }
  .back-amount { top: 225px; font-size: 77px; color: var(--paper); }
  .back-advance { top: 307px; font-size: 50px; color: var(--paper); }
</style>
</head>
<body>

<section class="card card-front" aria-label="Card front">
  <svg class="hill" width="687" height="390" viewBox="0 0 687 390" aria-hidden="true">
    <path d="M0,280 Q343.5,118 687,280 L687,390 L0,390 Z" fill="var(--brand-green)"/>
    <path d="M0,280 Q343.5,118 687,280" fill="none" stroke="var(--brand-red)" stroke-width="4"/>
  </svg>

  <div class="brand"><span class="brand-mark"></span>Northgate<br>Financial</div>
  <div class="divider"></div>

  <address class="address" style="font-style:normal">
    180 Harbor Ave<br>
    Ste 410<br>
    Country Name AB 5625
  </address>
  <div class="phone">
    <svg width="18" height="18" viewBox="0 0 24 24" aria-hidden="true">
      <path fill="var(--brand-red)" d="M6.6 10.8a15.1 15.1 0 0 0 6.6 6.6l2.2-2.2c.3-.3.7-.4 1-.2 1.1.4 2.3.6 3.6.6.6 0 1 .4 1 1V20c0 .6-.4 1-1 1A17 17 0 0 1 3 4c0-.6.4-1 1-1h3.5c.6 0 1 .4 1 1 0 1.3.2 2.5.6 3.6.1.3 0 .7-.2 1z"/>
    </svg>
    (555) 555-555
  </div>

  <div class="badge">FREE ESTIMATES!</div>
  <p class="line front-amount">UP TO <span class="figure">&amp;6000</span></p>
  <p class="line front-advance">SAME DAY ADVANCE</p>
  <p class="line front-note">ON APPROVED TAX RETURNS!</p>
</section>

<section class="card card-back" aria-label="Card back">
  <div class="back-top"></div>
  <div class="back-rule"></div>
  <p class="line back-file">FILE YOUR</p>
  <p class="line back-taxes">TAXES HERE</p>
  <p class="line back-amount">UP TO &amp;6000</p>
  <p class="line back-advance">SAME DAY ADVANCE</p>
</section>

</body>
</html>
```